Poster for Sparkler-style Christmas music and dance show.

I need a poster for a Christmas music and dance show styled after the Harbor Lane Sparklers. Attached are samples of posters for previous years. I like the font style and colors of the blue one. The design should contain an ornament design with dancers dancing on it. The dancers should be cartoon style, not photo real. A sample is attached.
The poster MUST contain the VelMUSE logo, sponsor logos, the dates (December 12-13, 2015), the location (Lia & Peter Hollins Theatre, 4150 Brindle Crest, Lakeway, TX), VelMUSE contact info (www.vel-muse.org and 512-640-3187 ext 204), and "Directed and Choreographed by Wesley Hartman."
Logos are all attached. Finalized files needed in sizes: 12x18, 4x6, and 30x48 inches.

Target Market(s)

Community Theatre patrons

Industry/Entity Type

Radio

Font styles to use
Serif

Colors
0792cd
33a6d7
85cae6
ecf7fb
ffffff

Requirements
Must have
• VelMUSE logo (attached)
• sponsor logos: Nadia Poll Photography, Brimwell Dentistry, Topside Grill, Up Tempo (attached)
• Show dates: December 12-13, 2015)
• Show Location: Lia & Peter Hollins Theatre, 4150 Brindle Crest, Lakeway, TX)
• VelMUSE contact info: www.vel-muse.org and 512-640-3187 ext 204
• "Directed and Choreographed by Wesley Hartman"
• An ornament design with dancers on it. The dancers should be cartoon style, not photo real. A sample of a dancer graphic is attached.
Nice to have
• snowflakes or other winter themes

```html
<!DOCTYPE html>
<html lang="en">
<head>
<meta charset="utf-8">
<title>Holiday Extravaganza – VelMUSE Broadway Company</title>
<link rel="stylesheet" href="https://fonts.googleapis.com/css2?family=Cinzel:wght@400;700&family=Lobster&family=Great+Vibes&family=Playfair+Display:wght@400;700;900&display=swap">
<style>
  :root {
    --blue-deep: #0792cd;
    --blue-mid: #33a6d7;
    --blue-soft: #85cae6;
    --blue-mist: #ecf7fb;
    --white: #ffffff;
    --navy: #17336e;
    --red: #c81f2b;
    --red-dark: #8e1119;
    --gold: #f3c64a;
    --cream: #f6e7c4;
    --ink: #111111;
  }
  * { box-sizing: border-box; margin: 0; padding: 0; }
  html, body { width: 753px; height: 1200px; overflow: hidden; }
  body { font-family: "Playfair Display", serif; }

  .poster {
    position: relative;
    width: 753px;
    height: 1200px;
    overflow: hidden;
    background: radial-gradient(ellipse at 50% 40%, var(--blue-mist) 0%, var(--blue-soft) 55%, var(--blue-mid) 100%);
  }

  .brand {
    position: absolute;
    top: 24px; left: 0; width: 100%;
    text-align: center;
  }
  .brand__name {
    font-family: "Cinzel", serif;
    font-weight: 700;
    font-size: 52px;
    letter-spacing: 2px;
    color: var(--navy);
    line-height: 1;
  }
  .brand__company {
    margin-top: 14px;
    font-family: "Cinzel", serif;
    font-weight: 700;
    font-size: 24px;
    letter-spacing: 2px;
    color: var(--navy);
  }
  .presents {
    position: absolute;
    top: 150px; left: 52px;
    font-family: "Great Vibes", cursive;
    font-size: 40px;
    color: var(--navy);
    z-index: 2;
  }

  .dancers-art {
    position: absolute;
    top: 190px; left: 80px;
    width: 600px; height: 420px;
    border-radius: 46% 46% 8% 8%;
    background: linear-gradient(180deg, var(--blue-mid) 0%, #4b5fb8 40%, #6a3f9e 75%, var(--blue-deep) 100%);
    opacity: 0.85;
  }

  .title {
    position: absolute;
    top: 570px; left: 0; width: 100%;
    text-align: center;
  }
  .title__holiday {
    font-family: "Lobster", cursive;
    font-weight: 400;
    font-size: 150px;
    line-height: 1;
    color: var(--red);
    text-shadow: 3px 3px 0 var(--gold), 6px 6px 8px rgba(0,0,0,0.35);
  }
  .title__ribbon {
    margin: 2px auto 0;
    width: 470px;
    height: 62px;
    background: linear-gradient(180deg, var(--red) 0%, var(--red-dark) 100%);
    clip-path: polygon(0 0, 100% 0, 95% 50%, 100% 100%, 0 100%, 5% 50%);
    font-family: "Playfair Display", serif;
    font-weight: 700;
    font-size: 38px;
    letter-spacing: 3px;
    line-height: 62px;
    color: var(--cream);
  }

  .credit {
    position: absolute;
    top: 822px; left: 0; width: 100%;
    text-align: center;
    color: var(--navy);
  }
  .credit__label { font-size: 21px; line-height: 1.2; }
  .credit__name {
    font-weight: 900;
    font-size: 34px;
    line-height: 1.2;
    color: var(--red);
    letter-spacing: 1px;
  }

  .details {
    position: absolute;
    top: 930px; left: 0; width: 100%;
    text-align: center;
    color: var(--navy);
    white-space: nowrap;
  }
  .details__dates {
    font-weight: 900;
    font-size: 31px;
    line-height: 1.2;
  }
  .details__venue {
    margin-top: 6px;
    font-weight: 700;
    font-size: 17px;
    line-height: 1.3;
  }
  .details__contact {
    margin-top: 4px;
    font-size: 16px;
    line-height: 1.3;
  }

  .sponsors {
    position: absolute;
    left: 14px; right: 14px; bottom: 28px;
    display: flex;
    align-items: center;
    gap: 10px;
  }
  .sponsors__label {
    font-size: 13px;
    color: var(--navy);
    width: 62px;
  }
  .sponsor {
    flex: 1;
    height: 66px;
    display: flex;
    align-items: center;
    justify-content: center;
    gap: 8px;
    font-family: "Playfair Display", serif;
    font-weight: 700;
    font-size: 16px;
    text-align: center;
    line-height: 1.1;
    padding: 0 8px;
  }
  .sponsor--light { background: var(--white); color: var(--ink); }
  .sponsor--dark { background: var(--ink); color: var(--white); }
  .sponsor__dot {
    width: 12px; height: 12px;
    border-radius: 50%;
    background: currentColor;
    flex: none;
  }
</style>
</head>
<body>
<main class="poster">
  <header class="brand">
    <div class="brand__name">VelMUSE</div>
    <div class="brand__company">VELMUSE BROADWAY COMPANY</div>
  </header>

  <div class="presents">Presents...</div>

  <div class="dancers-art" role="img" aria-label="Illustration of a line of dancer silhouettes in blue and purple tones"></div>

  <section class="title">
    <h1 class="title__holiday">Holiday</h1>
    <div class="title__ribbon">EXTRAVAGANZA</div>
  </section>

  <section class="credit">
    <div class="credit__label">Directed and Choreographed by</div>
    <div class="credit__name">WESLEY HARTMAN</div>
  </section>

  <section class="details">
    <div class="details__dates">TICKETS $$ • DECEMBER 12-13, 2015</div>
    <div class="details__venue">LIA &amp; PETER HOLLINS THEATRE, 4150 Brindle Crest, Lakeway, TX</div>
    <div class="details__contact">VelMUSE contact info (www.vel-muse.org and 512-640-3187 ext. 204)</div>
  </section>

  <footer class="sponsors">
    <div class="sponsors__label">Sponsors:</div>
    <div class="sponsor sponsor--light">Nadia Poll Photography</div>
    <div class="sponsor sponsor--light">Brimwell Dentistry</div>
    <div class="sponsor sponsor--dark"><span class="sponsor__dot"></span>Topside Grill</div>
    <div class="sponsor sponsor--dark">Up Tempo</div>
  </footer>
</main>
</body>
</html>
```